Looking for someone to design a business card for my plumbing business Quandor Plumbing Solutions I want the background also to be black, must attract clients. If possible I want the front to be the logo and the back to show maybe the details.

Target Market(s)

Clients

Industry/Entity Type

Plumbing maintenance

Contact Information for Business Card

Name: Felix, Contact: 0461 539 207, Email: quandorplumbingsolutions@mailbrook.example, Licence number 728093K

Font styles to use
Other font styles liked:
• as per logo maybe?

Colors

Designer to choose colors to be used in the design.

Requirements
Nice to have
• stating the service I provide, emergency plumbing, plumbing maintenance, drainage maintenance, block sewer and stormwater, camera and locating.

```html
<!DOCTYPE html>
<html lang="en">
<head>
<meta charset="utf-8">
<title>Quandor Plumbing Solutions – Business Card</title>
<link rel="stylesheet" href="https://fonts.googleapis.com/css2?family=Montserrat:wght@400;500;700;800&display=swap">
<style>
  :root {
    --stage: #4a4a4a;
    --card: #1f1f20;
    --blue: #4d93d3;
    --white: #ffffff;
    --muted: #e9e9e9;
  }
  * { box-sizing: border-box; margin: 0; padding: 0; }
  html, body { width: 1200px; height: 875px; overflow: hidden; }
  body {
    background: var(--stage);
    font-family: "Montserrat", sans-serif;
    position: relative;
  }
  .card {
    position: absolute;
    left: 290px;
    width: 620px;
    height: 380px;
    background: var(--card);
    border-radius: 18px;
    overflow: hidden;
    box-shadow: 0 12px 30px rgba(0,0,0,.35);
  }
  .card--front { top: 35px; }
  .card--back { top: 460px; }

  .brand { position: absolute; display: flex; align-items: center; gap: 14px; }
  .brand__mascot {
    background: linear-gradient(160deg, #ffffff 0%, #dfe6ee 70%, #4d93d3 100%);
    border-radius: 40% 40% 30% 30%;
  }
  .brand__name {
    color: var(--white);
    font-weight: 800;
    text-transform: uppercase;
    line-height: 1.05;
  }
  .card--front .brand { left: 150px; top: 70px; }
  .card--front .brand__mascot { width: 110px; height: 160px; }
  .card--front .brand__name { font-size: 30px; }
  .card--front .brand__name small { display: block; font-size: 17px; letter-spacing: 1px; }

  .services {
    position: absolute; left: 0; right: 0; top: 275px;
    text-align: center; color: var(--muted);
    font-size: 14px; line-height: 1.6; font-weight: 500;
  }
  .services .dot { color: var(--blue); margin: 0 6px; }

  .card--back .brand { left: 40px; top: 115px; gap: 10px; }
  .card--back .brand__mascot { width: 70px; height: 104px; }
  .card--back .brand__name { font-size: 19px; }
  .card--back .brand__name small { display: block; font-size: 11px; letter-spacing: .6px; }

  .divider {
    position: absolute; left: 296px; top: 55px;
    width: 1.5px; height: 130px; background: var(--blue);
  }
  .contact { position: absolute; left: 316px; top: 48px; color: var(--white); }
  .contact__name {
    color: var(--blue); font-weight: 800; font-size: 22px;
    text-transform: uppercase; letter-spacing: .5px; line-height: 1;
  }
  .contact__role { font-size: 13px; font-weight: 500; margin: 3px 0 12px; }
  .contact__list { list-style: none; font-size: 10.5px; line-height: 1.85; }
  .contact__list li { display: flex; align-items: center; gap: 7px; white-space: nowrap; }
  .contact__list svg { width: 10px; height: 10px; flex: none; }

  .wave { position: absolute; left: 0; top: 0; width: 620px; height: 380px; }
  .licence {
    position: absolute; right: 34px; bottom: 96px;
    color: var(--white); font-size: 13px; font-weight: 500;
    transform: rotate(-27deg); transform-origin: right bottom;
    white-space: nowrap;
  }
</style>
</head>
<body>

<section class="card card--front">
  <div class="brand">
    <div class="brand__mascot" role="img" aria-label="Mascot illustration of a hairy creature holding a pipe wrench"></div>
    <div class="brand__name">Quandor<small>Plumbing Solutions</small></div>
  </div>
  <p class="services">
    Emergency plumbing<span class="dot">•</span>Plumbing maintenance<span class="dot">•</span>Drainage maintenance<br>
    Block sewer and stormwater<span class="dot">•</span>Camera and locating
  </p>
</section>

<section class="card card--back">
  <svg class="wave" viewBox="0 0 620 380" aria-hidden="true">
    <path d="M140 380 C330 372 470 262 620 190 L620 206 C475 278 340 378 185 380 Z" fill="#ffffff"/>
    <path d="M185 380 C340 378 475 278 620 206 L620 380 Z" fill="#4d93d3"/>
  </svg>

  <div class="brand">
    <div class="brand__mascot" role="img" aria-label="Mascot illustration of a hairy creature holding a pipe wrench"></div>
    <div class="brand__name">Quandor<small>Plumbing Solutions</small></div>
  </div>

  <div class="divider"></div>

  <div class="contact">
    <p class="contact__name">Felix</p>
    <p class="contact__role">Founder &amp; CEO</p>
    <ul class="contact__list">
      <li>
        <svg viewBox="0 0 10 10"><path d="M2 0.5 L3.6 2.6 L2.8 3.6 C3.4 5 4.8 6.5 6.3 7.2 L7.3 6.4 L9.5 8 L8.3 9.5 C4.5 9.2 0.8 5.5 0.5 1.7 Z" fill="#4d93d3"/></svg>
        0461 539 207
      </li>
      <li>
        <svg viewBox="0 0 10 10"><rect x="0.5" y="2" width="9" height="6.5" fill="#4d93d3"/><path d="M0.8 2.3 L5 5.6 L9.2 2.3" stroke="#1f1f20" stroke-width="0.9" fill="none"/></svg>
        quandorplumbingsolutions@mailbrook.example
      </li>
      <li>
        <svg viewBox="0 0 10 10"><circle cx="5" cy="5" r="4.5" fill="#4d93d3"/></svg>
        @QuandorPlumbingSolutions
      </li>
    </ul>
  </div>

  <p class="licence">Licence number 728093K</p>
</section>

</body>
</html>
```